ebook cover for The Heron & The Teapot (Plink!)

We would like an ebook cover for a post Ph.D. on Animal Totems book called The Heron and The Teapot. It is about human relationships and dating. Author is Marla Wendlow Ph.D.
I am thinking perhaps just typographic with a fancy custom italicized or handwriting kind of font that fills the whole page, or a picture that doesn't belittle the fairytale of love. Something cosmic.
The subtitle to guide people, small, is "on dating"

```html
<!DOCTYPE html>
<html lang="en">
<head>
<meta charset="utf-8">
<title>The Heron and The Teapot — on dating</title>
<link rel="stylesheet" href="https://fonts.googleapis.com/css2?family=Yellowtail&family=Montserrat:wght@800&display=swap">
<style>
  :root {
    --sky-top: #2a0816;
    --sky-mid: #4b3532;
    --sky-low: #6f6a4c;
    --sky-bottom: #7f8259;
    --star: #ecd9a4;
    --title: #ffffff;
    --author: #561a22;
    --glow: #f4efb8;
    --warm-a: #d99a64;
    --warm-b: #c9b266;
  }
  * { margin: 0; padding: 0; box-sizing: border-box; }
  html, body { width: 754px; height: 1200px; overflow: hidden; background: var(--sky-top); }
  .cover {
    position: relative;
    width: 754px;
    height: 1200px;
    overflow: hidden;
    background: linear-gradient(180deg, var(--sky-top) 0%, var(--sky-mid) 38%, var(--sky-low) 62%, var(--sky-bottom) 100%);
  }
  .stars { position: absolute; inset: 0; width: 754px; height: 1200px; }
  .stars path { fill: var(--star); }
  .title {
    position: absolute;
    left: 0; right: 0;
    text-align: center;
    color: var(--title);
    font-family: "Yellowtail", cursive;
    font-weight: 400;
    line-height: 1;
    text-shadow: 0 2px 4px rgba(0,0,0,0.25);
  }
  .title-first { top: 112px; font-size: 150px; letter-spacing: 1px; }
  .title-joiner { top: 318px; font-size: 64px; }
  .title-second { top: 392px; font-size: 150px; }
  .subtitle {
    position: absolute;
    top: 602px; left: 0; right: 0;
    text-align: center;
    color: var(--title);
    font-family: "Yellowtail", cursive;
    font-size: 58px;
    line-height: 1;
    text-shadow: 0 2px 4px rgba(0,0,0,0.25);
  }
  .illustration {
    position: absolute;
    left: 0; top: 700px;
    width: 754px; height: 500px;
    background:
      radial-gradient(ellipse 180px 230px at 578px 300px, var(--warm-b) 0%, rgba(201,178,102,0.85) 55%, rgba(244,239,184,0) 100%),
      radial-gradient(ellipse 170px 190px at 170px 360px, var(--warm-a) 0%, rgba(217,154,100,0.85) 55%, rgba(244,239,184,0) 100%),
      radial-gradient(ellipse 420px 320px at 377px 330px, rgba(244,239,184,0.55) 0%, rgba(244,239,184,0) 100%);
  }
  .author {
    position: absolute;
    left: 0; right: 0;
    top: 1134px;
    text-align: center;
    color: var(--author);
    font-family: "Montserrat", sans-serif;
    font-weight: 800;
    font-size: 36px;
    letter-spacing: 0.5px;
  }
</style>
</head>
<body>
  <main class="cover">
    <svg class="stars" viewBox="0 0 754 1200" aria-hidden="true">
      <defs>
        <path id="star" d="M0,-15 L4.4,-4.8 L14.3,-4.6 L6.9,2.6 L8.8,12.1 L0,7.2 L-8.8,12.1 L-6.9,2.6 L-14.3,-4.6 L-4.4,-4.8 Z"/>
      </defs>
      <use href="#star" transform="translate(19 20)"/>
      <use href="#star" transform="translate(192 69)"/>
      <use href="#star" transform="translate(426 85)"/>
      <use href="#star" transform="translate(632 53)"/>
      <use href="#star" transform="translate(707 196)"/>
      <use href="#star" transform="translate(578 180) scale(0.8)"/>
      <use href="#star" transform="translate(78 371)"/>
      <use href="#star" transform="translate(250 395)"/>
      <use href="#star" transform="translate(684 405)"/>
    </svg>

    <h1>
      <span class="title title-first">The Heron</span>
      <span class="title title-joiner">and</span>
      <span class="title title-second">The Teapot</span>
    </h1>
    <p class="subtitle">on dating</p>

    <div class="illustration" role="img" aria-label="Illustration of a heron and a teapot side by side, softly glowing in warm tones"></div>

    <p class="author">Marla Wendlow Ph.D.</p>
  </main>
</body>
</html>
```